PowerPoint template for a tech startup

We need a PowerPoint template with a title slide, text slide, section slide, and thank you slide.
Our application helps engineering teams to be more productive. We would love a design that is slick, sophisticated, and consistent with our brand. (see more at www.velmo.ai or attached files)
By the way (not a requirement), Velmo means lighthouse in Greek.
Also, here is the font we used (not required) - https://glyphvault.net/fonts/league-gothic

• https://glyphvault.net/fonts/league-gothic

```html
<!DOCTYPE html>
<html lang="en">
<head>
<meta charset="utf-8">
<title>Velmo — Presentation Template</title>
<link rel="stylesheet" href="https://fonts.googleapis.com/css2?family=Poppins:ital,wght@0,400;0,500;0,600;0,700;1,400;1,500&display=swap">
<style>
:root{
  --page:#ffffff;
  --slide:#141414;
  --slide-edge:#0c0c0c;
  --band:#1d1d1d;
  --ink:#ffffff;
  --muted:#b9b9b9;
  --faint:#6f6f6f;
  --accent:#7d62ff;
  --rule:#3a3a3a;
}
*{box-sizing:border-box;margin:0;padding:0}
html,body{width:1143px;height:1200px;overflow:hidden;background:var(--page)}
body{position:relative;font-family:"Poppins",sans-serif;color:var(--ink)}
.slide{position:absolute;width:305px;height:171px;overflow:hidden;
  background:radial-gradient(circle at 70% 30%,#1e1e1e 0%,var(--slide) 55%,var(--slide-edge) 100%);
  box-shadow:0 4px 12px rgba(0,0,0,.35)}
.slide > *{position:absolute}
.brand{left:18px;top:9px;font-weight:700;font-size:8px;letter-spacing:.2px;color:var(--ink)}
.brand-hero{left:55px;top:77px;width:72px;font-size:18.5px;letter-spacing:.3px;line-height:1;white-space:nowrap}
.footer{left:0;bottom:0;width:100%;height:8px;background:var(--band);font-size:3.4px;color:var(--faint);line-height:8px}
.footer .url{position:absolute;left:23px}
.footer .num{position:absolute;right:24px}
.title{font-weight:600;line-height:1.18;color:var(--ink)}
.title em{font-style:normal;color:var(--accent)}
.t-md{font-size:12.5px}
.t-lg{font-size:20px;line-height:1}
.body{font-size:3.5px;line-height:1.6;color:var(--muted);text-align:justify}
.body b{color:var(--ink);font-weight:600}
.ph-laptop{background:linear-gradient(135deg,#5b6a78 0%,#2f3e52 40%,#8a7f73 75%,#3a3632 100%)}
.ph-team{background:linear-gradient(120deg,#c98945 0%,#e7e1d8 35%,#5c6b7c 70%,#2e3642 100%)}
.ph-city{background:linear-gradient(135deg,#6e68a8 0%,#cfc9ee 40%,#8f8ac4 65%,#4d4a7d 100%)}
.ph-keys{background:linear-gradient(160deg,#262a2e 0%,#55524c 45%,#a9a497 75%,#6b5d4c 100%)}
.ph-portrait{background:linear-gradient(160deg,#8c6a55 0%,#d9b79c 45%,#2e2e32 100%)}
.ph-portrait-light{background:linear-gradient(160deg,#d8d6d2 0%,#c9a389 45%,#3a3a3e 100%)}
.feature{text-align:center;width:62px}
.feature svg{display:block;margin:0 auto 3px;width:8px;height:8px}
.feature h4{font-size:3.6px;font-style:italic;font-weight:600;margin-bottom:2px}
.feature p{font-size:3px;line-height:1.55;color:var(--muted)}
.step{width:60px;display:flex;gap:3px}
.step .n{font-size:4.5px;font-style:italic;color:var(--ink)}
.step p{font-size:3px;line-height:1.55;color:var(--muted)}
.member{width:66px;text-align:center}
.member .photo{position:static;width:66px;height:51px}
.member h5{font-size:3.4px;font-weight:600;margin-top:2px}
.member span{display:block;font-size:2.6px;color:var(--accent)}
.list-item{width:120px;display:flex;gap:8px}
.list-item svg{flex:none;width:9px;height:9px}
.list-item h4{font-size:4px;font-style:italic;font-weight:500;margin-bottom:2px}
.list-item p{font-size:3.2px;line-height:1.55;color:var(--muted)}
.sub{font-size:5.5px;font-weight:600}
.sub em{font-style:normal;color:var(--accent)}
</style>
</head>
<body>

<!-- 1 Title -->
<section class="slide" style="left:47px;top:70px">
  <div class="brand brand-hero">VELMO</div>
  <h1 class="title t-md" style="left:143px;top:66px">Your Title<br>Presentation<br><em>Goes Here</em></h1>
</section>

<!-- 2 Title alt -->
<section class="slide" style="left:419px;top:70px">
  <div class="brand brand-hero">VELMO</div>
  <h1 class="title t-md" style="left:143px;top:66px">Your Title<br>Presentation<br><em>Goes Here</em></h1>
</section>

<!-- 3 About -->
<section class="slide" style="left:792px;top:70px">
  <div class="brand">VELMO</div>
  <h2 class="title" style="left:18px;top:44px;font-size:14px">About <em>Us</em></h2>
  <p class="body" style="left:17px;top:72px;width:134px">Velmo gives engineering teams one calm place to see their <b>work</b>. We pull code, reviews and tickets into a single view, so leads can find blockers early, plan with real data and keep delivery steady. Teams spend less time in meetings and more time building the product their users need.</p>
  <div class="photo ph-laptop" role="img" aria-label="Young man working on a laptop outdoors" style="left:177px;top:9px;width:128px;height:156px"></div>
  <div class="footer"><span class="url">www.velmo.ai</span><span class="num">3</span></div>
</section>

<!-- 4 Text with photo -->
<section class="slide" style="left:47px;top:292px">
  <div class="brand">VELMO</div>
  <div class="photo ph-team" role="img" aria-label="Team working together at laptops around a table" style="left:0;top:30px;width:134px;height:134px"></div>
  <h2 class="title t-md" style="left:149px;top:30px">Your Title<br>Presentation<br><em>Goes Here</em></h2>
  <p class="body" style="left:149px;top:87px;width:134px">Velmo gives engineering teams one calm place to see their <b>work</b>. We pull code, reviews and tickets into a single view, so leads can find blockers early, plan with real data and keep delivery steady. Teams spend less time in meetings and more time building the product their users need.</p>
  <div class="footer"><span class="url">www.velmo.ai</span><span class="num">4</span></div>
</section>

<!-- 5 Two photos -->
<section class="slide" style="left:419px;top:292px">
  <div class="brand">VELMO</div>
  <div class="photo ph-city" role="img" aria-label="City skyline blended with hands at a keyboard" style="left:21px;top:22px;width:85px;height:68px"></div>
  <div class="photo ph-city" role="img" aria-label="Hands typing blended with city buildings" style="left:110px;top:22px;width:170px;height:68px"></div>
  <h2 class="title t-md" style="left:21px;top:102px">Your Title Slide<br><em>Goes Here</em></h2>
  <p class="body" style="left:135px;top:104px;width:155px">Clear metrics for every sprint help teams focus on the <b>work</b> that matters most and ship with confidence.</p>
  <p class="body" style="left:135px;top:126px;width:155px">Clear metrics for every sprint help teams focus on the <b>work</b> that matters most and ship with confidence.</p>
  <div class="footer"><span class="url">www.velmo.ai</span><span class="num">5</span></div>
</section>

<!-- 6 Three photos -->
<section class="slide" style="left:792px;top:292px">
  <div class="brand">VELMO</div>
  <h2 class="title t-md" style="left:45px;top:33px">Your Title<br>Slide<br><em>Goes Here</em></h2>
  <p class="body" style="left:132px;top:37px;width:145px">Velmo gives engineering teams one calm place to see their <b>work</b>. We pull code, reviews and tickets into a single view, so leads can find blockers early, plan with real data and keep delivery steady. Teams spend less time in meetings and more time building the product their users need.</p>
  <div class="photo ph-laptop" role="img" aria-label="Man working on a laptop" style="left:42px;top:93px;width:65px;height:60px"></div>
  <div class="photo ph-team" role="img" aria-label="Team at a shared table" style="left:120px;top:93px;width:65px;height:60px"></div>
  <div class="photo ph-city" role="img" aria-label="Hands typing over a city skyline" style="left:199px;top:93px;width:106px;height:60px"></div>
  <div class="footer"><span class="url">www.velmo.ai</span><span class="num">6</span></div>
</section>

<!-- 7 Vision -->
<section class="slide" style="left:47px;top:515px">
  <div class="brand">VELMO</div>
  <div class="photo ph-keys" role="img" aria-label="Hands typing on a keyboard" style="left:42px;top:25px;width:263px;height:61px"></div>
  <div style="left:23px;top:99px;width:165px;height:1px;background:var(--rule)"></div>
  <div style="left:106px;top:99px;width:82px;height:1px;background:var(--accent)"></div>
  <h2 class="title t-lg" style="left:22px;top:107px">Our <em>vision</em></h2>
  <p style="left:26px;top:130px;font-size:2.8px;color:var(--muted)">Short caption here</p>
  <div class="step" style="left:148px;top:111px"><span class="n">01</span><p>Short note on this point.</p></div>
  <div class="step" style="left:224px;top:111px"><span class="n">03</span><p>Short note on this point.</p></div>
  <div class="step" style="left:148px;top:133px"><span class="n">02</span><p>Short note on this point.</p></div>
  <div class="step" style="left:224px;top:133px"><span class="n">04</span><p>Short note on this point.</p></div>
  <div class="footer"><span class="url">www.velmo.ai</span><span class="num">7</span></div>
</section>

<!-- 8 Service quote -->
<section class="slide" style="left:419px;top:515px">
  <div class="brand">VELMO</div>
  <h2 class="title t-lg" style="left:23px;top:33px">Our <em>service</em></h2>
  <p style="left:24px;top:62px;width:122px;font-size:5px;line-height:1.65;font-style:italic;color:var(--muted)">“ Tools that let engineers focus on building, not on chasing status.</p>
  <div class="photo ph-city" role="img" aria-label="City skyline blended with a person at work" style="left:25px;top:102px;width:116px;height:47px"></div>
  <div class="feature" style="left:158px;top:38px"><svg viewBox="0 0 10 10"><circle cx="5" cy="3" r="2" fill="#fff"/><rect x="1.5" y="6" width="7" height="3" rx="1" fill="#fff"/></svg><h4>Text Tittle Here</h4><p>Short note on this point.</p></div>
  <div class="feature" style="left:236px;top:38px"><svg viewBox="0 0 10 10"><rect x="1" y="1" width="8" height="6" rx="1" fill="none" stroke="#fff"/><rect x="3" y="8" width="4" height="1" fill="#fff"/></svg><h4>Text Tittle Here</h4><p>Short note on this point.</p></div>
  <div class="feature" style="left:158px;top:93px"><svg viewBox="0 0 10 10"><rect x="0.5" y="3" width="6" height="4" fill="#fff"/><rect x="6.5" y="4.5" width="3" height="2.5" fill="#fff"/><circle cx="2.5" cy="8" r="1" fill="#fff"/><circle cx="7.5" cy="8" r="1" fill="#fff"/></svg><h4>Text Tittle Here</h4><p>Short note on this point.</p></div>
  <div class="feature" style="left:236px;top:93px"><svg viewBox="0 0 10 10"><path d="M1 5 L4 3 L6 5 L9 3 L9 6 L6 8 L4 6 L1 7Z" fill="#fff"/></svg><h4>Text Tittle Here</h4><p>Short note on this point.</p></div>
  <div class="footer"><span class="url">www.velmo.ai</span><span class="num">8</span></div>
</section>

<!-- 9 Two columns -->
<section class="slide" style="left:792px;top:515px">
  <div class="brand">VELMO</div>
  <div class="photo ph-keys" role="img" aria-label="Hands typing on a keyboard" style="left:20px;top:27px;width:76px;height:68px"></div>
  <div class="photo ph-team" role="img" aria-label="Colleagues discussing around laptops" style="left:110px;top:27px;width:171px;height:69px"></div>
  <h2 class="title" style="left:0;width:305px;top:98px;text-align:center;font-size:11.5px">Your Title <em>Slide Goes Here</em></h2>
  <p class="body" style="left:26px;top:117px;width:68px">Clear metrics for every sprint help teams focus on the work that matters most and ship with confidence.</p>
  <p class="body" style="left:114px;top:117px;width:165px">Velmo gives engineering teams one calm place to see their work. We pull code, reviews and tickets into a single view, so leads can find blockers early, plan with real data and keep delivery steady. Teams spend less time in meetings and more time building the product their users need.</p>
  <div class="footer"><span class="url">www.velmo.ai</span><span class="num">9</span></div>
</section>

<!-- 10 Text and photos -->
<section class="slide" style="left:47px;top:737px">
  <div class="brand">VELMO</div>
  <h2 class="title t-md" style="left:24px;top:23px">Your Title<br><em>Slide Goes<br>Here</em></h2>
  <div style="left:24px;top:77px;width:78px;height:1px;background:var(--rule)"></div>
  <p class="body" style="left:24px;top:80px;width:77px">Velmo gives engineering teams one calm place to see their work. We pull code, reviews and tickets into a single view, so leads can find blockers early, plan with real data and keep delivery steady. Teams spend less time in meetings and more time building the product their users need.</p>
  <p class="body" style="left:124px;top:46px;width:47px">Clear metrics for every sprint help teams focus on the work that matters most and ship with confidence.</p>
  <p class="body" style="left:124px;top:115px;width:47px">Clear metrics for every sprint help teams focus on the work that matters most and ship with confidence.</p>
  <div class="photo ph-laptop" role="img" aria-label="Man smiling at a laptop" style="left:182px;top:23px;width:103px;height:56px"></div>
  <div class="photo ph-keys" role="img" aria-label="Hands typing on a keyboard" style="left:182px;top:93px;width:103px;height:56px"></div>
  <div class="footer"><span class="url">www.velmo.ai</span><span class="num">10</span></div>
</section>

<!-- 11 Team -->
<section class="slide" style="left:419px;top:737px">
  <div class="brand">VELMO</div>
  <h2 class="title" style="left:0;width:305px;top:10px;text-align:center;font-size:12px">Our <em>team</em></h2>
  <div class="member" style="left:17px;top:36px"><div class="photo ph-portrait" role="img" aria-label="Portrait of a team member"></div><h5>Dana Kerr</h5><span>Role Here</span></div>
  <div class="member" style="left:116px;top:36px"><div class="photo ph-portrait-light" role="img" aria-label="Portrait of a team member"></div><h5>Dana Kerr</h5><span>Role Here</span></div>
  <div class="member" style="left:216px;top:36px"><div class="photo ph-portrait-light" role="img" aria-label="Portrait of a team member"></div><h5>Dana Kerr</h5><span>Role Here</span></div>
  <div class="member" style="left:17px;top:99px"><div class="photo ph-portrait-light" role="img" aria-label="Portrait of a team member"></div><h5>Dana Kerr</h5><span>Role Here</span></div>
  <div class="member" style="left:116px;top:99px"><div class="photo ph-portrait" role="img" aria-label="Portrait of a team member"></div><h5>Dana Kerr</h5><span>Role Here</span></div>
  <div class="member" style="left:216px;top:99px"><div class="photo ph-portrait-light" role="img" aria-label="Portrait of a team member"></div><h5>Dana Kerr</h5><span>Role Here</span></div>
  <div class="footer"><span class="url">www.velmo.ai</span><span class="num">11</span></div>
</section>

<!-- 12 Service with photo -->
<section class="slide" style="left:792px;top:737px">
  <div class="brand">VELMO</div>
  <div class="photo ph-city" role="img" aria-label="City skyline blended with a person at work" style="left:28px;top:40px;width:117px;height:61px"></div>
  <h2 class="title t-lg" style="left:163px;top:35px">Our <em>service</em></h2>
  <p class="body" style="left:164px;top:62px;width:121px">Velmo gives engineering teams one calm place to see their work. We pull code, reviews and tickets into a single view, so leads can find blockers early, plan with real data and keep delivery steady. Teams spend less time in meetings and more time building the product their users need.</p>
  <div class="feature" style="left:32px;top:113px"><svg viewBox="0 0 10 10"><circle cx="3" cy="3.5" r="1.5" fill="#fff"/><circle cx="7" cy="3.5" r="1.5" fill="#fff"/><rect x="1" y="6" width="8" height="3" rx="1" fill="#fff"/></svg><h4>Text Tittle Here</h4><p>Short note on this point.</p></div>
  <div class="feature" style="left:125px;top:113px"><svg viewBox="0 0 10 10"><rect x="1" y="1" width="8" height="8" fill="none" stroke="#fff"/><rect x="3" y="5" width="1" height="3" fill="#fff"/><rect x="5" y="3" width="1" height="5" fill="#fff"/><rect x="7" y="4" width="1" height="4" fill="#fff"/></svg><h4>Text Tittle Here</h4><p>Short note on this point.</p></div>
  <div class="feature" style="left:218px;top:113px"><svg viewBox="0 0 10 10"><circle cx="5" cy="5" r="4" fill="none" stroke="#fff"/><circle cx="5" cy="5" r="2" fill="none" stroke="#fff"/><circle cx="5" cy="5" r=".8" fill="#fff"/></svg><h4>Text Tittle Here</h4><p>Short note on this point.</p></div>
  <div class="footer"><span class="url">www.velmo.ai</span><span class="num">12</span></div>
</section>

<!-- 13 Service centered -->
<section class="slide" style="left:47px;top:960px">
  <div class="brand">VELMO</div>
  <h2 class="title t-lg" style="left:0;width:305px;top:20px;text-align:center">Our <em>service</em></h2>
  <p class="body" style="left:37px;top:50px;width:231px;text-align:center">Velmo gives engineering teams one calm place to see their work. We pull code, reviews and tickets into a single view, so leads can find blockers early, plan with real data and keep delivery steady. Teams spend less time in meetings and more time building the product their users need.</p>
  <div class="feature" style="left:30px;top:93px"><svg viewBox="0 0 10 10"><rect x="1" y="1" width="6" height="4" fill="none" stroke="#fff"/><rect x="1" y="7" width="1" height="2" fill="#fff"/><rect x="3.5" y="7" width="1" height="2" fill="#fff"/><rect x="6" y="7" width="1" height="2" fill="#fff"/><rect x="0.5" y="6" width="8" height=".8" fill="#fff"/></svg><h4 style="margin-top:6px">Text Tittle Here</h4><p>Short note on this point.</p></div>
  <div style="left:140px;top:86px;width:27px;height:27px;border-radius:50%;background:#d9d9dc"></div>
  <svg style="left:149px;top:95px;width:9px;height:9px" viewBox="0 0 10 10"><rect x="1" y="2" width="8" height="5.5" rx="1" fill="none" stroke="#7d62ff"/><rect x="3.5" y="8.2" width="3" height=".9" fill="#7d62ff"/></svg>
  <div class="feature" style="left:122px;top:115px"><h4>Text Tittle Here</h4><p>Short note on this point.</p></div>
  <div class="feature" style="left:216px;top:93px"><svg viewBox="0 0 10 10"><circle cx="4" cy="4" r="3" fill="none" stroke="#fff"/><rect x="3" y="7" width="2" height="2" fill="#fff"/><path d="M7 4 H9.5" stroke="#fff"/></svg><h4 style="margin-top:6px">Text Tittle Here</h4><p>Short note on this point.</p></div>
  <div class="footer"><span class="url">www.velmo.ai</span><span class="num">13</span></div>
</section>

<!-- 14 Service list -->
<section class="slide" style="left:419px;top:960px">
  <div class="brand">VELMO</div>
  <div class="photo ph-keys" role="img" aria-label="Hands typing on a keyboard" style="left:164px;top:9px;width:141px;height:153px"></div>
  <p style="left:282px;top:16px;font-size:2.6px;color:var(--ink)">Modern Style</p>
  <h2 class="title" style="left:26px;top:19px;font-size:19px;line-height:1">Our <em>service</em></h2>
  <p class="body" style="left:28px;top:44px;width:125px;text-align:left">Clear metrics for every sprint help teams focus on the work that matters most and ship with confidence.</p>
  <div class="list-item" style="left:31px;top:70px"><svg viewBox="0 0 10 10"><circle cx="4" cy="6" r="2.5" fill="none" stroke="#fff" stroke-width="1.3"/><circle cx="7.5" cy="2.5" r="1.5" fill="none" stroke="#fff"/></svg><div><h4>Text Tittle Here</h4><p>Short note on this point.</p></div></div>
  <div class="list-item" style="left:31px;top:100px"><svg viewBox="0 0 10 10"><circle cx="5" cy="5" r="2" fill="none" stroke="#fff"/><path d="M5 .5V2M5 8v1.5M.5 5H2M8 5h1.5M2 2l1 1M7 7l1 1M8 2L7 3M2 8l1-1" stroke="#fff" stroke-width=".7"/></svg><div><h4>Text Tittle Here</h4><p>Short note on this point.</p></div></div>
  <div class="list-item" style="left:31px;top:130px"><svg viewBox="0 0 10 10"><path d="M5 .5L9 2v3c0 2.5-2 4-4 4.5C3 9 1 7.5 1 5V2Z" fill="#fff"/><path d="M3.3 5L4.6 6.3 7 3.8" stroke="#141414" fill="none"/></svg><div><h4>Text Tittle Here</h4><p>Short note on this point.</p></div></div>
  <div class="footer" style="width:164px"><span class="url">www.velmo.ai</span><span class="num">14</span></div>
</section>

<!-- 15 Subtitles -->
<section class="slide" style="left:792px;top:960px">
  <div class="brand">VELMO</div>
  <h2 class="title t-md" style="left:24px;top:31px">Your Title<br><em>Slide Goes<br>Here</em></h2>
  <p class="sub" style="left:103px;top:31px">Your SubTitle <em>Goes Here</em></p>
  <p class="body" style="left:103px;top:42px;width:110px">Clear metrics for every sprint help teams focus on the work that matters most and ship with confidence.</p>
  <div class="photo ph-laptop" role="img" aria-label="Man working on a laptop" style="left:226px;top:30px;width:67px;height:59px"></div>
  <div class="photo ph-city" role="img" aria-label="City skyline blended with a person at work" style="left:21px;top:92px;width:100px;height:60px"></div>
  <p class="sub" style="left:131px;top:95px">Your SubTitle <em>Goes Here</em></p>
  <p class="body" style="left:131px;top:105px;width:163px">Velmo gives engineering teams one calm place to see their work. We pull code, reviews and tickets into a single view, so leads can find blockers early, plan with real data and keep delivery steady. Teams spend less time in meetings and more time building the product their users need.</p>
  <div class="footer"><span class="url">www.velmo.ai</span><span class="num">15</span></div>
</section>

</body>
</html>
```